Brell Stone Company Business Cards

Front and Back Business Card - logo and text setup - cool design. I need workable photoshop or illustrator files so I can setup each employee card with design that is created
Updates

Hi everyone, thank you for the great entries. Please no more white and blue cards - there are so many already - black and silver only now please. thanks!

Target Market(s)

Construction Industry - Facility Managers

Industry/Entity Type

Construction

Contact Information for Business Card

I really like contemporary simplistic looks - clean neat....not opposed to seeing some black backrounds

Requirements
Must have
• Logo/website address with design on front only - www.brellstone-example.com (logo attached)
• Back:
• Name/Title/Company Address/Phone/email address
Nice to have
• Cool design
Should not have
• Nothing gimmicky like Fire or Water - since we are a Fire Protection company - it has all been done

```html
<!DOCTYPE html>
<html lang="en">
<head>
<meta charset="utf-8">
<title>Brell Stone Company Business Cards</title>
<link href="https://fonts.googleapis.com/css2?family=Poppins:wght@300;400;700;800&family=Oswald:wght@600&display=swap" rel="stylesheet">
<style>
  :root {
    --backdrop: #4a4a4b;
    --card: #2e2e30;
    --silver: #b8b8ba;
    --white: #f2f2f2;
    --orange: #ef4b2b;
    --blue: #2f4f9a;
    --rule: #ef4b2b;
  }
  * { box-sizing: border-box; margin: 0; padding: 0; }
  html, body { width: 1200px; height: 1200px; overflow: hidden; }
  body {
    background: var(--backdrop);
    font-family: "Poppins", sans-serif;
    position: relative;
  }
  .card {
    position: absolute;
    background: var(--card);
    border-radius: 22px;
    box-shadow: 0 18px 40px rgba(0,0,0,.45);
    color: var(--white);
  }
  /* Front */
  .card-front {
    left: 50px; top: 420px;
    width: 630px; height: 360px;
  }
  .front-brand {
    position: absolute;
    left: 70px; top: 120px;
    display: flex; align-items: center; gap: 16px;
  }
  .brand-mark {
    width: 26px; height: 26px;
    background: var(--silver);
  }
  .front-brand .brand-name {
    font-weight: 800;
    font-size: 44px;
    letter-spacing: -1px;
    color: var(--silver);
    line-height: 1;
  }
  .front-web {
    position: absolute;
    right: 44px; bottom: 40px;
    font-size: 17px;
    font-weight: 300;
    letter-spacing: .5px;
    color: var(--white);
  }
  .front-web .accent { color: var(--orange); font-weight: 400; }

  /* Back */
  .card-back {
    left: 770px; top: 285px;
    width: 370px; height: 630px;
    padding: 54px 40px;
  }
  .back-brand {
    font-weight: 800;
    font-size: 27px;
    letter-spacing: -.5px;
    line-height: 1.05;
    color: var(--blue);
    text-align: right;
  }
  .person { margin-top: 56px; }
  .person-name {
    font-family: "Oswald", sans-serif;
    font-weight: 600;
    font-size: 28px;
    letter-spacing: .5px;
    color: var(--orange);
    text-transform: uppercase;
    line-height: 1.1;
  }
  .person-title {
    font-size: 17px;
    font-weight: 300;
    margin-top: 4px;
  }
  .contacts { margin-top: 42px; list-style: none; }
  .contact {
    display: flex; align-items: center; gap: 16px;
    margin-bottom: 26px;
    font-size: 15px;
    font-weight: 300;
  }
  .contact-icon {
    flex: none;
    width: 28px; height: 28px;
    border-radius: 50%;
    background: var(--orange);
    display: flex; align-items: center; justify-content: center;
  }
  .contact-rule {
    height: 1px;
    width: 100%;
    background: var(--rule);
    margin: -12px 0 14px 44px;
    max-width: 60px;
  }
  .address { line-height: 1.5; }
</style>
</head>
<body>

  <section class="card card-front" aria-label="Card front">
    <div class="front-brand">
      <span class="brand-mark"></span>
      <span class="brand-name">Brell Stone Company</span>
    </div>
    <p class="front-web">www.<span class="accent">brellstone-example</span>.com</p>
  </section>

  <section class="card card-back" aria-label="Card back">
    <p class="back-brand">Brell Stone<br>Company</p>

    <div class="person">
      <h1 class="person-name">Dana Corwell</h1>
      <p class="person-title">Senior Consultant</p>
    </div>

    <ul class="contacts">
      <li class="contact">
        <span class="contact-icon">
          <svg width="14" height="14" viewBox="0 0 24 24"><path fill="#fff" d="M6.6 10.8a15.5 15.5 0 0 0 6.6 6.6l2.2-2.2c.3-.3.7-.4 1-.2 1.1.4 2.3.6 3.6.6.6 0 1 .4 1 1V20c0 .6-.4 1-1 1A17 17 0 0 1 3 4c0-.6.4-1 1-1h3.5c.6 0 1 .4 1 1 0 1.3.2 2.5.6 3.6.1.3 0 .7-.2 1z"/></svg>
        </span>
        <span>555.014.2290</span>
      </li>
      <li class="contact-rule"></li>
      <li class="contact">
        <span class="contact-icon">
          <svg width="14" height="14" viewBox="0 0 24 24"><rect x="3" y="6" width="18" height="12" fill="none" stroke="#fff" stroke-width="2"/><path d="M3 6l9 7 9-7" fill="none" stroke="#fff" stroke-width="2"/></svg>
        </span>
        <span>info@brellstone-example.com</span>
      </li>
      <li class="contact-rule"></li>
      <li class="contact">
        <span class="contact-icon">
          <svg width="14" height="14" viewBox="0 0 24 24" fill="none" stroke="#fff" stroke-width="2"><circle cx="12" cy="12" r="9"/><path d="M3 12h18M12 3c3 3 3 15 0 18M12 3c-3 3-3 15 0 18"/></svg>
        </span>
        <span>www.brellstone-example.com</span>
      </li>
      <li class="contact-rule"></li>
      <li class="contact">
        <span class="contact-icon">
          <svg width="14" height="14" viewBox="0 0 24 24"><path fill="#fff" d="M12 2a7 7 0 0 0-7 7c0 5 7 13 7 13s7-8 7-13a7 7 0 0 0-7-7zm0 9.5A2.5 2.5 0 1 1 12 6.5a2.5 2.5 0 0 1 0 5z"/></svg>
        </span>
        <span class="address">48 Harbor Works Rd<br>Millbrook, NY 10000</span>
      </li>
    </ul>
  </section>

</body>
</html>
```